Storm Restoration Contractor needs a professional letterhead design

Looking for a professional letterhead design. Not looking for your cheapo MS Word standard ones that are readily available. Dont want it to be cookie cutter look like ones readily available online. We just recently changed our logo and want to freshen up all our documents. Our company handles restoring a property back to a pre-loss condition after a storm damages it. For example, wind, hail, flood, fire losses.

Target Market(s)

Property Owners, Homeowners, Property Owners, Commercial Property Owners, Property Management Companies

Industry/Entity Type

Construction Company

Requirements
Must have
• Professional, Use 1 of 2 logo options
• Storm Restoration, Roofing, Siding, Windows

```html
<!DOCTYPE html>
<html lang="en">
<head>
<meta charset="utf-8">
<title>Haven Exteriors – Letterhead</title>
<link rel="stylesheet" href="https://fonts.googleapis.com/css2?family=Questrial&display=swap">
<style>
  :root {
    --backdrop: #bdbdbd;
    --paper: #f1f1f1;
    --brand-blue: #2466b0;
    --ink: #3c3c3c;
    --rule-grey: #a9a9a9;
  }
  * { box-sizing: border-box; margin: 0; padding: 0; }
  html, body {
    width: 1200px;
    height: 1041px;
    overflow: hidden;
    background: var(--backdrop);
    font-family: "Questrial", "Century Gothic", sans-serif;
  }
  .letterhead {
    position: absolute;
    left: 210px;
    top: 16px;
    width: 780px;
    height: 1009px;
    background: var(--paper);
    box-shadow: 0 2px 6px rgba(0,0,0,0.25);
  }
  .brand {
    position: absolute;
    left: 64px;
    top: 58px;
    display: flex;
    align-items: center;
    gap: 14px;
  }
  .brand-mark {
    width: 66px;
    height: 66px;
    border-radius: 50%;
    background: var(--brand-blue);
  }
  .brand-name {
    color: var(--brand-blue);
    font-size: 27px;
    line-height: 1.05;
    letter-spacing: 1.5px;
    text-transform: uppercase;
  }
  .contact {
    position: absolute;
    left: 576px;
    top: 68px;
    color: var(--ink);
    font-size: 10.5px;
    line-height: 13.7px;
  }
  .contact-line {
    display: flex;
    align-items: center;
    gap: 6px;
  }
  .contact-icon {
    width: 11px;
    height: 11px;
    flex: none;
  }
  .address {
    margin-top: 7px;
  }
  .footer-rule {
    position: absolute;
    top: 967px;
    height: 3px;
    background: var(--rule-grey);
  }
  .footer-rule.left { left: 0; width: 567px; }
  .footer-rule.right { left: 716px; width: 64px; }
  .website {
    position: absolute;
    left: 584px;
    top: 961px;
    font-size: 10.5px;
    letter-spacing: 0.3px;
    color: var(--ink);
  }
  .website strong {
    color: var(--brand-blue);
    font-weight: normal;
  }
  .footer-band {
    position: absolute;
    left: 0;
    top: 979px;
    width: 780px;
    height: 14px;
    background: var(--brand-blue);
  }
</style>
</head>
<body>
  <main class="letterhead">
    <header class="brand">
      <span class="brand-mark" aria-hidden="true"></span>
      <div class="brand-name">Haven<br>Exteriors</div>
    </header>

    <address class="contact" style="font-style: normal;">
      <div class="contact-line">
        <svg class="contact-icon" viewBox="0 0 11 11" aria-hidden="true">
          <rect width="11" height="11" rx="2" fill="var(--brand-blue)"/>
          <path d="M3.2 2.3 L4.4 3.8 L3.8 4.6 Q4.6 6.3 6.4 7.2 L7.2 6.6 L8.7 7.8 L7.9 8.8 Q4.4 8.4 2.2 3.1 Z" fill="#fff"/>
        </svg>
        <span>480-555-0142</span>
      </div>
      <div class="contact-line">
        <svg class="contact-icon" viewBox="0 0 11 11" aria-hidden="true">
          <rect width="11" height="11" rx="2" fill="var(--brand-blue)"/>
          <rect x="3.5" y="2" width="4" height="2.5" fill="#fff"/>
          <rect x="2.2" y="4.8" width="6.6" height="3" fill="#fff"/>
          <rect x="3.5" y="7.2" width="4" height="2" fill="#fff"/>
        </svg>
        <span>480-555-0142</span>
      </div>
      <div class="contact-line">
        <svg class="contact-icon" viewBox="0 0 11 11" aria-hidden="true">
          <rect width="11" height="11" rx="2" fill="var(--brand-blue)"/>
          <rect x="2.2" y="3.2" width="6.6" height="4.6" fill="#fff"/>
          <path d="M2.2 3.2 L5.5 5.9 L8.8 3.2" stroke="var(--brand-blue)" stroke-width="0.8" fill="none"/>
        </svg>
        <span>info@havenext.com</span>
      </div>
      <div class="address">
        4720 N Ridgeline Road STE 210<br>
        Tempe, AZ 85281
      </div>
    </address>

    <footer>
      <div class="footer-rule left"></div>
      <div class="website">WWW.<strong>HAVENEXT</strong>.COM</div>
      <div class="footer-rule right"></div>
      <div class="footer-band"></div>
    </footer>
  </main>
</body>
</html>
```